VocaTerrana Community/ Talent Gallery

VocaTerrana is developing a collaborative career course, with coaching and community exchange. Goal is to offer a platform where talented candidates can show their expertise and find projects, partners, and develop their online portfolios!

Here is a good example of the type of thing we hope to create with focus on sustainability focused talent to task matching
http://www.brambleforth.com/global-themes/employment-and-growth/connecting-talent-with-opportunity-in-the-digital-age

We hope to have a "grid style" gallery where it is easy to search by talent types and focus areas within the scope of "Sustainability" issues...Food/Water/Energy, Public Health, Technology, Sustainable Cities, Infrastructure, Education, Policy, Emerging Economies, Ecosystems, Social Innovation, inclusive Security, Equity Issues. For each topic/ header we hope to have candidates post their completed portfolios to exhibit resumes, biography, a case study... they may actually prepare these on other sites, but can link in OR alternately that they can easily create here, similar to "pinqo.io" ....

Hope to include a blog space titled "Rising over the Rift", where people can mix it up across these topic issues as they are interdependent and often require partners across discipline areas! If possible another area where jobs related to these issues may be posted as project or job opportunities by potential employers.

If there is a way to create a feed from various job sites that already exist...like Jobora...or http://www.greenledgerworks.com/ that would be super great. Again...sort of a portal connection to bridge the gap ....instead of candidates having to search all the time, we are hoping they can advertise their talent and employers may search here for these well presented portfolios!

Target Market(s)

Educators, Students, Career Transitioners, Employers, Professional Associations, Talent Recruiters with focus on Sustainability related Talent to Task matching!

Industry/Entity Type

Sustainability

Number of Pages Required

4 page

Font styles to use
Sans Serif

Colors
3176b5
32b8a4
add136

Requirements
Must have
• Not sure about the coded/ uncoded option here....
• Must have - grid style area where Sustainability Professionals with varied focus areas can exhibit their talent portfolios
• appear as a Talent Gallery that starts with photos & obvious organization...other tabs to be in a menu.
• ability to search both talent and task opportunity areas to help coaches or community members make matches....some topic focused category or tag words to help make them searchable...???
• consistent professional styling to existing website and new artflock postcard shared in brief/ images area
• Interactive blog space where articles, issues may be posted, discussed
• Bulletin board or feed for project opportunities to be posted where candidates may locate them and/or employers may express specific "call" for talent..These may be Short term Internships, Projects, Consulting Team Opportunity, or Jobs/ part time to full time....
Nice to have
• A calendar area where we can post networking opportunities, issues presentations where potential partners can meet the next generation leaders, attend a forum or webinar presentation.
Should not have
• Too much text on front page...Should be clean design,

```html
<!DOCTYPE html>
<html lang="en">
<head>
<meta charset="utf-8">
<title>VocaTerrana – Collaborative Career Course</title>
<link href="https://fonts.googleapis.com/css2?family=Lato:wght@400;700;900&display=swap" rel="stylesheet">
<style>
:root{
  --blue:#3176b5;
  --blue-deep:#2a67a3;
  --teal:#32b8a4;
  --teal-deep:#1a8a80;
  --green:#add136;
  --green-deep:#7fae1e;
  --ink:#222a33;
  --body:#555b62;
  --navy:#0e2437;
  --navy-deep:#081826;
  --line:#d9dde2;
}
*{box-sizing:border-box;margin:0;padding:0}
html,body{width:1200px;height:3888px;overflow:hidden}
body{position:relative;font-family:'Lato',Arial,sans-serif;color:var(--ink);background:#fff}
.abs{position:absolute}
a{color:inherit;text-decoration:none}

/* header */
.site-header{left:0;top:0;width:1200px;height:135px;background:#fff}
.topbar{left:661px;top:0;width:539px;height:36px;background:var(--blue);color:#fff;font-size:14px;display:flex;align-items:center;gap:28px;padding-left:26px}
.topbar svg{vertical-align:-3px;margin-right:6px}
.login{left:1011px;top:0;width:90px;height:36px;background:var(--green);color:var(--ink);font-weight:700;font-size:17px;display:flex;align-items:center;justify-content:center}
.header-band{left:0;top:112px;width:1200px;height:23px;background:linear-gradient(var(--teal-deep),var(--teal))}
.brand-dot{left:104px;top:8px;width:100px;height:100px;border-radius:50%;background:var(--teal);border:5px solid #fff;box-shadow:0 2px 6px rgba(0,0,0,.2)}
.brand-name{left:214px;top:56px;font-size:27px;font-weight:700;color:var(--teal-deep)}
.main-nav{top:62px;font-size:17px;color:var(--ink)}
.main-nav.active{color:var(--blue);font-weight:700}
.nav-ring{left:628px;top:50px;width:58px;height:44px;border-radius:22px;background:#eef3f7}

/* hero */
.hero{left:0;top:135px;width:1200px;height:570px;background:radial-gradient(ellipse at 50% 60%,#8c8c8c 0%,#5a5a5a 40%,#2c2c2c 80%,#1a1a1a 100%)}
.hero-plant{left:440px;top:190px;width:260px;height:180px;border-radius:50%;background:radial-gradient(circle,#7fbf3a 0%,rgba(127,191,58,0) 70%)}
.hero-title{left:98px;top:305px;color:#fff;font-size:33px;font-weight:900;line-height:41px}
.btn-start{left:98px;top:495px;height:46px;padding:0 26px 0 58px;border-radius:23px;background:var(--green);color:var(--ink);font-weight:700;font-size:17px;display:flex;align-items:center}
.btn-dot{position:absolute;left:-2px;top:-3px;width:52px;height:52px;border-radius:50%;background:var(--teal);border:3px solid #fff}
.arrow{top:400px;width:34px;height:34px;border-radius:50%;background:rgba(255,255,255,.18);display:flex;align-items:center;justify-content:center}

/* separator mark */
.sep{width:62px;height:62px;border-radius:50%;background:var(--teal);border:5px solid #fff;box-shadow:0 1px 4px rgba(0,0,0,.25);left:569px}

/* headings */
.h2{font-size:40px;font-weight:900;color:var(--ink)}
.h2 span{color:var(--teal-deep)}
.h2.center{left:0;width:1200px;text-align:center}
.rule{height:2px;background:var(--line)}

.btn-read{height:34px;padding:0 20px 0 48px;border-radius:17px;background:var(--green);color:var(--ink);font-weight:700;font-size:15px;display:flex;align-items:center}
.btn-read i{position:absolute;left:-2px;top:-3px;width:40px;height:40px;border-radius:50%;background:var(--teal);border:3px solid #fff}

/* mission */
.mission-text{left:98px;top:830px;width:550px;font-size:13.5px;line-height:21px;color:var(--body)}
.mission-photo{left:752px;top:757px;width:349px;height:246px;background:radial-gradient(circle at 50% 50%,#a7b7c4 0%,#c9cfd4 50%,#9aa1a6 100%);border:4px solid #e9ecef}

/* services */
.services{left:0;top:1050px;width:1200px;height:578px;background:linear-gradient(var(--blue),var(--blue-deep))}
.svc-title{color:#fff}
.svc-rule{left:500px;top:1178px;width:200px;height:2px;background:rgba(255,255,255,.5)}
.svc-hub{left:446px;top:1234px;width:300px;height:300px;border-radius:50%;background:var(--teal-deep);border:8px solid rgba(255,255,255,.9)}
.svc-item{color:#fff;width:220px}
.svc-item h3{font-size:17px;font-weight:700;margin-bottom:8px}
.svc-item p{font-size:12.5px;line-height:17px;opacity:.9}
.svc-item.right-al{text-align:right}

/* phases */
.phase-intro{left:245px;top:1752px;width:710px;text-align:center;font-size:13.5px;line-height:21px;color:var(--body)}
.card{width:241px}
.card-photo{width:241px;height:192px;border:3px solid #c8cdd2}
.card-dot{left:101px;top:172px;width:40px;height:40px;border-radius:50%;background:var(--teal);border:3px solid #fff}
.card h3{position:absolute;top:229px;width:241px;text-align:center;font-size:18px;font-weight:900}
.card p{position:absolute;top:258px;width:241px;text-align:center;font-size:13px;color:var(--body)}
.card-bar{position:absolute;top:282px;left:0;width:241px;height:8px;border-top:2px solid #e3e6e9}
.card-plus{position:absolute;top:279px;left:111px;width:20px;height:20px;border-radius:50%;color:#fff;font-size:16px;font-weight:900;line-height:20px;text-align:center}

/* gallery */
.gallery{left:0;top:2260px;width:1200px;height:630px;background:linear-gradient(var(--teal-deep),#167c73)}
.gal-deco{border-radius:50%;background:rgba(255,255,255,.06)}
.tile{overflow:hidden}
.tile .cap{position:absolute;left:0;bottom:0;width:100%;height:28px;background:rgba(0,0,0,.72);color:#fff;font-size:14px;font-weight:700;display:flex;align-items:center;justify-content:center}
.view-more{left:1016px;top:2659px;width:85px;height:141px;background:#0e2437;color:#fff;font-weight:700;font-size:15px;line-height:18px;display:flex;align-items:flex-end;justify-content:center;text-align:center;padding-bottom:14px}

/* blog */
.post{width:290px}
.post-photo{width:290px;height:168px}
.date{left:6px;top:0;width:56px;height:62px;background:var(--blue);color:#fff;text-align:center}
.date b{display:block;font-size:24px;font-weight:900;line-height:36px}
.date span{display:block;height:26px;background:var(--green);color:var(--ink);font-weight:700;font-size:13px;line-height:26px}
.post h3{position:absolute;top:190px;font-size:16px;font-weight:700}
.post p{position:absolute;top:215px;width:280px;font-size:12.5px;line-height:17px;color:var(--body)}
.post .more{position:absolute;top:272px;border:2px solid #8a9096;padding:3px 9px;font-size:12px;font-weight:700}

/* footer */
.footer{left:0;top:3440px;width:1200px;height:396px;background:var(--navy)}
.foot-nav{top:3525px;font-size:16px;color:#fff}
.foot-h{top:3588px;font-size:20px;color:var(--teal)}
.foot-row{color:#fff;font-size:13.5px;display:flex;gap:12px;align-items:flex-start}
.field{left:454px;width:254px;height:30px;border:1px solid #7690a8;background:#1d3950;color:#fff;font-size:13px;padding:6px 10px}
.submit{left:454px;top:3776px;width:118px;height:34px;background:var(--teal);color:#fff;font-weight:700;font-size:17px;display:flex;align-items:center;justify-content:center}
.feed{left:824px;color:#fff;font-size:13.5px;line-height:18px}
.feed small{display:block;color:#a9b6c2;font-size:12.5px}
.bottom{left:0;top:3836px;width:1200px;height:52px;background:var(--navy-deep);color:#fff;font-size:13px}
.social{top:3850px;width:26px;height:26px;border-radius:50%}
</style>
</head>
<body>

<!-- header -->
<header class="abs site-header">
  <div class="abs topbar" style="color:#fff">
    <span><svg width="14" height="14" viewBox="0 0 24 24"><path fill="#fff" d="M6.6 10.8a15.1 15.1 0 006.6 6.6l2.2-2.2c.3-.3.7-.4 1-.2 1.1.4 2.3.6 3.6.6.6 0 1 .4 1 1V20c0 .6-.4 1-1 1A17 17 0 013 4c0-.6.4-1 1-1h3.5c.6 0 1 .4 1 1 0 1.3.2 2.5.6 3.6.1.3 0 .7-.2 1z"/></svg>202-555-0147</span>
    <span><svg width="15" height="12" viewBox="0 0 24 18"><rect x="1" y="1" width="22" height="16" fill="none" stroke="#fff" stroke-width="2"/><path d="M1 1l11 9 11-9" fill="none" stroke="#fff" stroke-width="2"/></svg>info@vocaterrana.com</span>
  </div>
  <a class="abs login" href="#">Log In</a>
  <div class="abs header-band"></div>
  <div class="abs brand-dot"></div>
  <div class="abs brand-name">VocaTerrana</div>
  <div class="abs nav-ring"></div>
  <a class="abs main-nav active" style="left:636px" href="#">Home</a>
  <a class="abs main-nav" style="left:726px" href="#">About Us</a>
  <a class="abs main-nav" style="left:834px" href="#">Services</a>
  <a class="abs main-nav" style="left:938px" href="#">Blog</a>
  <a class="abs main-nav" style="left:1013px" href="#">Contact Us</a>
</header>

<!-- hero -->
<section class="abs hero" role="img" aria-label="Black and white photo of hands framing a seedling held in cupped palms"></section>
<div class="abs hero-plant"></div>
<h1 class="abs hero-title">We Are Developing<br>A Collaborative Career<br>Course With Coaching &amp;<br>Community Exchange</h1>
<a class="abs btn-start" href="#"><i class="btn-dot"></i>Get Start Now</a>
<div class="abs arrow" style="left:32px"><svg width="10" height="14" viewBox="0 0 10 14"><path d="M8 1L2 7l6 6" stroke="#fff" stroke-width="2.5" fill="none"/></svg></div>
<div class="abs arrow" style="left:1134px"><svg width="10" height="14" viewBox="0 0 10 14"><path d="M2 1l6 6-6 6" stroke="#fff" stroke-width="2.5" fill="none"/></svg></div>
<div class="abs sep" style="top:672px"></div>

<!-- mission -->
<h2 class="abs h2" style="left:98px;top:748px">Our <span>Mission &amp; Philosophy</span></h2>
<div class="abs rule" style="left:98px;top:806px;width:550px"></div>
<p class="abs mission-text">Our mission is to cultivate a community of learning and professional practice to support career transitions and next generation leadership of sustainable solutions that balance economic, environment, and equity as we meet local-to-global change. Individual inquiry and creative talent development are facilitated by professional coaches, activated through experiential learning projects, informed by a network of professionals from sustainability focused organizations.</p>
<a class="abs btn-read" style="left:104px;top:970px" href="#"><i></i>Read More</a>
<div class="abs mission-photo" role="img" aria-label="Overhead photo of a team in a circle holding puzzle pieces together"></div>

<!-- services -->
<section class="abs services"></section>
<h2 class="abs h2 center svc-title" style="top:1098px;font-size:34px">Our Services</h2>
<div class="abs svc-rule"></div>
<svg class="abs" style="left:0;top:1050px" width="1200" height="578">
  <g stroke="rgba(255,255,255,.45)" stroke-width="1.5" fill="none">
    <path d="M390 258 H520 L560 230"/>
    <path d="M800 258 H680 L640 230"/>
    <path d="M390 438 H500 L530 410"/>
    <path d="M800 438 H690 L660 410"/>
  </g>
  <!-- icons -->
  <g fill="#fff">
    <circle cx="338" cy="162" r="9"/><path d="M322 196c0-14 7-22 16-22s16 8 16 22z"/><rect x="300" y="170" width="14" height="3"/><rect x="362" y="170" width="14" height="3"/>
    <rect x="808" y="158" width="44" height="30" rx="3" fill="none" stroke="#fff" stroke-width="3"/><rect x="822" y="190" width="16" height="6"/><circle cx="856" cy="188" r="9"/>
    <rect x="312" y="362" width="44" height="9" rx="3"/><rect x="316" y="374" width="44" height="9" rx="3"/><rect x="310" y="386" width="48" height="10" rx="3"/>
    <rect x="820" y="354" width="40" height="24" rx="2" fill="none" stroke="#fff" stroke-width="3"/><circle cx="830" cy="388" r="6"/><circle cx="850" cy="388" r="6"/><path d="M818 408c0-8 5-12 12-12s12 4 12 12z M838 408c0-8 5-12 12-12s12 4 12 12z"/>
  </g>
</svg>
<div class="abs svc-hub" role="img" aria-label="Large brand emblem circle"></div>
<div class="abs svc-item right-al" style="left:164px;top:1285px"><h3>Next Generation Talent</h3><p>Lorem ipsum dolor sit amet,<br>consectetuer adipiscing elit, sed<br>diam nonummy nibh euismod...[+]</p></div>
<div class="abs svc-item" style="left:804px;top:1285px"><h3>Online Coaching</h3><p>Lorem ipsum dolor sit amet,<br>consectetuer adipiscing elit, sed<br>diam nonummy nibh euismod...[+]</p></div>
<div class="abs svc-item right-al" style="left:164px;top:1484px"><h3>Courses</h3><p>Lorem ipsum dolor sit amet,<br>consectetuer adipiscing elit, sed<br>diam nonummy nibh euismod...[+]</p></div>
<div class="abs svc-item" style="left:804px;top:1484px"><h3>In-Person Coaching</h3><p>Lorem ipsum dolor sit amet,<br>consectetuer adipiscing elit, sed<br>diam nonummy nibh euismod...[+]</p></div>
<div class="abs sep" style="top:1600px"></div>

<!-- four phase -->
<h2 class="abs h2 center" style="top:1674px;font-size:34px">Four <span>Phase Career Course</span></h2>
<div class="abs rule" style="left:460px;top:1730px;width:280px"></div>
<p class="abs phase-intro">Through a proven four-phase process, integrating principles of lifelong learning, career transitions, entrepreneurship, change management, and innovation, our interdisciplinary, collaborative course is designed to guide you through creative change for career, lifestyle and/or next generation leadership.</p>
<a class="abs btn-read" style="left:540px;top:1834px" href="#"><i></i>Read More</a>

<div class="abs card" style="left:96px;top:1913px;height:300px">
  <div class="card-photo" role="img" aria-label="Photo of hands joining coloured puzzle pieces" style="background:linear-gradient(135deg,#d7dde3,#a9b4be)"></div>
  <div class="abs card-dot"></div><h3>CLARIFY</h3><p>Personal Profile, Vision &amp; Mission</p>
  <div class="card-bar"></div><div class="card-plus" style="background:var(--blue)">+</div>
</div>
<div class="abs card" style="left:350px;top:1913px;height:300px">
  <div class="card-photo" role="img" aria-label="Photo of colleagues talking around a meeting table" style="background:linear-gradient(135deg,#e6e8ea,#9fb0c0)"></div>
  <div class="abs card-dot"></div><h3>COMMUNICATE</h3><p>Personal Profile, Vision &amp; Mission</p>
  <div class="card-bar"></div><div class="card-plus" style="background:var(--teal-deep)">+</div>
</div>
<div class="abs card" style="left:604px;top:1913px;height:300px">
  <div class="card-photo" role="img" aria-label="Photo of a team stacking hands together" style="background:linear-gradient(135deg,#cfd4d9,#7c8792)"></div>
  <div class="abs card-dot"></div><h3>COLLABORATE</h3><p>Personal Profile, Vision &amp; Mission</p>
  <div class="card-bar"></div><div class="card-plus" style="background:var(--green)">+</div>
</div>
<div class="abs card" style="left:860px;top:1913px;height:300px">
  <div class="card-photo" role="img" aria-label="Photo of a person facing a wall of glowing sketched ideas" style="background:linear-gradient(135deg,#6d8fb0,#243a55)"></div>
  <div class="abs card-dot"></div><h3>CREATE</h3><p>Personal Profile, Vision &amp; Mission</p>
  <div class="card-bar"></div><div class="card-plus" style="background:var(--blue)">+</div>
</div>

<!-- gallery -->
<section class="abs gallery"></section>
<div class="abs gal-deco" style="left:980px;top:2300px;width:230px;height:230px"></div>
<div class="abs gal-deco" style="left:-60px;top:2640px;width:200px;height:200px"></div>
<h2 class="abs h2 center" style="top:2306px;font-size:34px;color:#fff">Our Gallery</h2>
<div class="abs" style="left:500px;top:2362px;width:200px;height:2px;background:rgba(255,255,255,.5)"></div>

<div class="abs tile" style="left:98px;top:2410px;width:213px;height:390px;background:linear-gradient(#f0a13a,#5b3316 75%,#1d1209)" role="img" aria-label="Silhouette of construction cranes at sunset"><div class="cap">Infrastructure</div></div>
<div class="abs tile" style="left:327px;top:2410px;width:347px;height:182px;background:radial-gradient(circle at 50% 60%,#eef2f4,#b3c0c8)" role="img" aria-label="Light bulb with a small plant growing inside"><div class="cap">Food/ Water/ Energy</div></div>
<div class="abs tile" style="left:327px;top:2608px;width:347px;height:192px;background:linear-gradient(135deg,#b7b7b7,#555)" role="img" aria-label="Black and white photo of hands with words written on the palms"><div class="cap">Public Health</div></div>
<div class="abs tile" style="left:690px;top:2410px;width:212px;height:234px;background:linear-gradient(#b9d3e8,#5f8d5e 60%,#3e6a3d)" role="img" aria-label="Aerial view of a green city skyline"><div class="cap">Sustainable Cities</div></div>
<div class="abs tile" style="left:918px;top:2410px;width:183px;height:234px;background:linear-gradient(135deg,#e9edf0,#8e9aa6)" role="img" aria-label="Presenter teaching a small group at a whiteboard"><div class="cap">Education</div></div>
<div class="abs tile" style="left:690px;top:2659px;width:310px;height:141px;background:linear-gradient(135deg,#2c82c9,#0d2f63)" role="img" aria-label="Blue digital circuit board"><div class="cap">Technology</div></div>
<a class="abs view-more" href="#">View<br>More</a>
<div class="abs sep" style="top:2862px"></div>

<!-- blog -->
<h2 class="abs h2 center" style="top:2958px;font-size:34px">Rising Over <span>The Rift</span></h2>
<div class="abs rule" style="left:480px;top:3014px;width:240px"></div>

<article class="abs post" style="left:104px;top:3077px;height:300px">
  <div class="post-photo" role="img" aria-label="Stepping stones across calm water" style="background:linear-gradient(#dfe3e6,#8b9298)"></div>
  <div class="abs date"><b>23</b><span>JUN</span></div>
  <h3>Ecosystem Insights for Leaders</h3>
  <p>As an offering for leaders engaged in systems change, we offer seven important lessons from our work with thousands of educators,</p>
  <a class="more" href="#">Read More</a>
</article>
<article class="abs post" style="left:454px;top:3077px;height:300px">
  <div class="post-photo" role="img" aria-label="Book cover on a warm orange background" style="background:linear-gradient(135deg,#c46a27,#3b1f0f)"></div>
  <div class="abs date"><b>23</b><span>JUN</span></div>
  <h3>Sustainable Development ?</h3>
  <p>Alden Marsh has recently published his book, The Era of Shared Prosperity, which offers a helpful synthesis of data....</p>
  <a class="more" href="#">Read More</a>
</article>
<article class="abs post" style="left:809px;top:3077px;height:300px">
  <div class="post-photo" role="img" aria-label="Grilled steak with vegetables on a plate" style="background:radial-gradient(circle at 50% 60%,#a8552a,#e7dcc9 75%)"></div>
  <div class="abs date"><b>23</b><span>JUN</span></div>
  <h3>Food Security</h3>
  <p>Maybe we do not eat all the same types of things, depending on whether you are a human being, animal or plant....</p>
  <a class="more" href="#">Read More</a>
</article>

<!-- footer -->
<footer class="abs footer"></footer>
<div class="abs sep" style="top:3410px"></div>
<a class="abs foot-nav" style="left:368px" href="#">Home</a>
<a class="abs foot-nav" style="left:456px" href="#">About Us</a>
<a class="abs foot-nav" style="left:566px" href="#">Services</a>
<a class="abs foot-nav" style="left:670px" href="#">Blog</a>
<a class="abs foot-nav" style="left:745px" href="#">Contact Us</a>

<h4 class="abs foot-h" style="left:98px">Contact Details</h4>
<div class="abs foot-row" style="left:104px;top:3640px;width:260px">
  <svg width="12" height="16" viewBox="0 0 12 16"><path d="M6 0a6 6 0 016 6c0 4.5-6 10-6 10S0 10.5 0 6a6 6 0 016-6z" fill="#fff"/><circle cx="6" cy="6" r="2.2" fill="#0e2437"/></svg>
  <span>3025- Lorem ipsum dolor sit amet,<br>consectetuer adipiscing - 12354</span></div>
<div class="abs foot-row" style="left:104px;top:3697px"><svg width="13" height="13" viewBox="0 0 24 24"><path fill="#fff" d="M6.6 10.8a15.1 15.1 0 006.6 6.6l2.2-2.2c.3-.3.7-.4 1-.2 1.1.4 2.3.6 3.6.6.6 0 1 .4 1 1V20c0 .6-.4 1-1 1A17 17 0 013 4c0-.6.4-1 1-1h3.5c.6 0 1 .4 1 1 0 1.3.2 2.5.6 3.6.1.3 0 .7-.2 1z"/></svg><span>202-555-0147</span></div>
<div class="abs foot-row" style="left:104px;top:3740px"><svg width="13" height="13" viewBox="0 0 24 24"><path fill="#fff" d="M6.6 10.8a15.1 15.1 0 006.6 6.6l2.2-2.2c.3-.3.7-.4 1-.2 1.1.4 2.3.6 3.6.6.6 0 1 .4 1 1V20c0 .6-.4 1-1 1A17 17 0 013 4c0-.6.4-1 1-1h3.5c.6 0 1 .4 1 1 0 1.3.2 2.5.6 3.6.1.3 0 .7-.2 1z"/></svg><span>202-555-0147</span></div>
<div class="abs foot-row" style="left:104px;top:3790px"><svg width="14" height="11" viewBox="0 0 24 18"><rect x="1" y="1" width="22" height="16" fill="none" stroke="#fff" stroke-width="2"/><path d="M1 1l11 9 11-9" fill="none" stroke="#fff" stroke-width="2"/></svg><span>info@vocaterrana.com</span></div>

<h4 class="abs foot-h" style="left:454px">Quick Inquiry</h4>
<div class="abs field" style="top:3650px">Name</div>
<div class="abs field" style="top:3692px">Email</div>
<div class="abs field" style="top:3734px">Message</div>
<a class="abs submit" href="#">Submit</a>

<h4 class="abs foot-h" style="left:824px">View Feeds</h4>
<div class="abs feed" style="top:3640px;font-size:14px;letter-spacing:.3px">GREEN HORIZON JOBS</div>
<div class="abs feed" style="top:3666px">• Education Development Coordinator<small>&nbsp;&nbsp;Civic Canopy Council</small><small style="font-size:10px">&nbsp;&nbsp;&nbsp;view more connections</small></div>
<div class="abs feed" style="top:3724px">• Environmental Communications Specialist<small>&nbsp;&nbsp;Northfield Analytics Group, Inc.</small></div>
<div class="abs feed" style="top:3766px">• Sales Coordinator<small>&nbsp;&nbsp;Reclaimwell, Inc</small></div>

<div class="abs bottom"><span class="abs" style="left:98px;top:18px">Copyright © 2016 VocaTerrana. All Rights Reserved.</span></div>
<div class="abs social" style="left:959px;background:var(--blue)"></div>
<div class="abs social" style="left:995px;background:var(--blue)"></div>
<div class="abs social" style="left:1031px;background:var(--blue)"></div>
<div class="abs social" style="left:1067px;background:#c9473f"></div>

</body>
</html>
```